Estate Planning Law Firm opening new branch in Florida

I am an experienced estate planning attorney that recently relocated to Florida. Looking for a banner Ad to place on platforms such as HomeLane, Chatterbox and Picturely to create publicity for firm and new leads.

```html
<!DOCTYPE html>
<html lang="en">
<head>
<meta charset="utf-8">
<title>Calmwater Law Firm – Estate & Financial Planning</title>
<link rel="stylesheet" href="https://fonts.googleapis.com/css2?family=Noto+Serif:wght@700;800&family=Montserrat:wght@500;600;700&display=swap">
<style>
  :root{
    --teal:#1e6b6d;
    --teal-bright:#1f7a78;
    --navy:#2c3a4f;
    --navy-light:#3a4a61;
    --ink:#2b3a50;
    --white:#ffffff;
    --photo-warm:#d9c9b4;
    --photo-cool:#b9b3c2;
  }
  *{margin:0;padding:0;box-sizing:border-box}
  html,body{width:1200px;height:628px;overflow:hidden;background:var(--white)}
  .banner{position:relative;width:1200px;height:628px;overflow:hidden;background:var(--white);font-family:"Montserrat",sans-serif}
  .backdrop{position:absolute;inset:0}
  .brand{position:absolute;left:60px;top:36px;display:flex;align-items:center;gap:14px}
  .brand-square{width:46px;height:46px;background:var(--teal)}
  .brand-name{font-family:"Noto Serif",serif;font-weight:700;color:var(--ink);line-height:1}
  .brand-name .firm{display:block;font-size:40px;letter-spacing:2px}
  .brand-name .suffix{display:block;font-size:15px;letter-spacing:2px;margin-top:6px;padding-left:70px}
  .headline{position:absolute;left:60px;top:160px;font-family:"Noto Serif",serif;font-weight:800;color:var(--teal);font-size:43px;line-height:70px;letter-spacing:.5px}
  .locale{position:absolute;left:60px;top:483px;color:var(--white);font-weight:600;font-size:15px;letter-spacing:.2px}
  .cta-label{position:absolute;left:60px;top:536px;color:var(--white);font-weight:700;font-size:20px}
  .phone{position:absolute;left:60px;top:574px;display:flex;align-items:center;gap:14px;color:var(--white);font-weight:600;font-size:27px}
  .phone-icon{width:30px;height:30px;background:var(--white);border-radius:5px;display:flex;align-items:center;justify-content:center}
  .ref-code{position:absolute;right:34px;bottom:20px;color:var(--white);font-weight:600;font-size:14px}
</style>
</head>
<body>
<div class="banner">
  <svg class="backdrop" width="1200" height="628" viewBox="0 0 1200 628">
    <defs>
      <linearGradient id="photoTone" x1="0" y1="0" x2="1" y2="1">
        <stop offset="0" stop-color="#e8e0d2"/>
        <stop offset=".5" stop-color="var(--photo-warm)"/>
        <stop offset="1" stop-color="var(--photo-cool)"/>
      </linearGradient>
    </defs>
    <path d="M0 338 C120 400 260 440 420 410 C520 392 600 370 700 340 L1200 240 L1200 628 L0 628 Z" fill="var(--teal-bright)"/>
    <path d="M0 372 C130 420 280 458 440 430 C540 412 620 390 720 362 L1200 262 L1200 628 L0 628 Z" fill="var(--navy)"/>
    <rect x="330" y="540" width="870" height="88" fill="var(--navy-light)" role="img" aria-label="Faint city skyline silhouette"/>
    <circle cx="868" cy="305" r="285" fill="var(--white)"/>
    <circle cx="868" cy="305" r="276" fill="url(#photoTone)" role="img" aria-label="Photo of a smiling senior couple reviewing documents with an advisor"/>
  </svg>

  <div class="brand">
    <div class="brand-square"></div>
    <div class="brand-name"><span class="firm">CALMWATER</span><span class="suffix">LAW FIRM, PLLC</span></div>
  </div>

  <h1 class="headline">ESTATE PLANNING &amp;<br>FINANCIAL PLANNING<br>UNDER ONE ROOF</h1>

  <p class="locale">MELBOURNE, FL ESTATE AND FINANCIAL PLANNING</p>
  <p class="cta-label">CALL NOW:</p>
  <p class="phone">
    <span class="phone-icon">
      <svg width="20" height="20" viewBox="0 0 24 24"><path fill="var(--navy)" d="M6.6 10.8a15.1 15.1 0 0 0 6.6 6.6l2.2-2.2c.3-.3.7-.4 1-.2 1.1.4 2.3.6 3.6.6.6 0 1 .4 1 1V20c0 .6-.4 1-1 1A17 17 0 0 1 3 4c0-.6.4-1 1-1h3.5c.6 0 1 .4 1 1 0 1.3.2 2.5.6 3.6.1.3 0 .7-.2 1z"/></svg>
    </span>
    (555) 014-2288
  </p>
  <p class="ref-code">C52</p>
</div>
</body>
</html>
```